Advertising company unique advertising platform

we need a logo design for a new company based in Australia Melbourne. We develop innovated advertising platform where consumer can use this platform to get regular discount, as business owner they can use this platform for free advertisement. Payment for this advertisement platform only payable every two weeks, when I generate revenue for their business

Industry/Entity Type

Advertising

Contact Information for Business Card

Dale Morven | Co-Founder |Managing Director
Suite 718 240 Wattlebrook Lane Melbourne Vic 3000

ABN 38 614 207 923
Tel: +61 0487 259 318 | Email: dale.morven@plivorantu.com

Font styles to use
Decorative
Script

Requirements
Must have
• Try few different design and some round corner business card
Should not have
• One round corner business card...try 4 different colour background not only black, make sure two side is designed. Be creative so imagine you are giving this to a client make sure has wow factor, if you can also try one design with engrave like all the logo, words look 3d feel
• The word Advertising Platform use attached file font

```html
<!DOCTYPE html>
<html lang="en">
<head>
<meta charset="utf-8">
<title>Kestra Loop – Business Card</title>
<link href="https://fonts.googleapis.com/css2?family=Roboto+Condensed:wght@400;700&display=swap" rel="stylesheet">
<style>
  :root {
    --stage: #3a332e;
    --card-dark: #232323;
    --card-dark-edge: #2c2c2c;
    --orange-core: #fbb23a;
    --orange-mid: #f5782c;
    --orange-edge: #e9462b;
    --accent-top: #2ec3f0;
    --accent-mid: #7f9de0;
    --accent-bottom: #22e6a8;
    --brand: #f5782c;
    --ink-dark: #1d1410;
    --ink-light: #e9e9e9;
  }
  * { box-sizing: border-box; margin: 0; padding: 0; }
  html, body {
    width: 1200px; height: 886px; overflow: hidden;
    background: var(--stage);
    font-family: "Roboto Condensed", "Arial Narrow", sans-serif;
  }
  .canvas { position: relative; width: 1200px; height: 886px; }
  .card {
    position: absolute; top: 285px;
    width: 540px; height: 315px;
    border-radius: 22px; overflow: hidden;
    background: linear-gradient(160deg, var(--card-dark-edge), var(--card-dark));
    box-shadow: 0 14px 30px rgba(0,0,0,.45);
  }
  .card--front { left: 40px; }
  .card--contact { left: 620px; }

  /* front side */
  .brand-lockup {
    position: absolute; left: 0; right: 0; top: 112px;
    display: flex; align-items: center; justify-content: center; gap: 14px;
  }
  .brand-dot { width: 34px; height: 34px; border-radius: 50%; background: var(--brand); }
  .brand-name {
    font-weight: 700; font-size: 40px; color: var(--brand); letter-spacing: 1px;
  }
  .website {
    position: absolute; left: 0; right: 0; top: 232px; text-align: center;
    color: var(--ink-light); font-size: 14px; letter-spacing: 6px;
  }

  /* contact side */
  .contact-brand {
    position: absolute; left: 0; top: 0; width: 215px; height: 315px;
    display: flex; align-items: center; justify-content: center;
  }
  .contact-brand .brand-name { font-size: 30px; }
  .info-panel {
    position: absolute; left: 215px; top: 0; width: 325px; height: 315px;
    background: radial-gradient(circle at 50% 55%, var(--orange-core) 0%, var(--orange-mid) 45%, var(--orange-edge) 100%);
  }
  .accent-strip {
    position: absolute; right: 0; top: 0; width: 12px; height: 315px;
    background: linear-gradient(180deg, var(--accent-top), var(--accent-mid) 50%, var(--accent-bottom));
  }
  .info-block {
    position: absolute; left: 5px; top: -5px; width: 315px; height: 325px;
    transform: rotate(-90deg);
    display: flex; flex-direction: column; align-items: center; justify-content: center;
    text-align: center; color: var(--ink-dark); font-size: 15px; line-height: 1.3;
  }
  .person-name { font-weight: 700; font-size: 21px; letter-spacing: .5px; }
  .person-role { font-size: 16px; margin-bottom: 12px; }
  .icon { width: 12px; height: 12px; display: block; margin: 3px auto; fill: var(--ink-dark); }
  .contact-line { margin-bottom: 2px; }
  .gap { height: 12px; }
</style>
</head>
<body>
<main class="canvas">
  <section class="card card--front" aria-label="Card front">
    <div class="brand-lockup">
      <span class="brand-dot"></span>
      <span class="brand-name">Kestra Loop</span>
    </div>
    <p class="website">www.plivorantu.com</p>
  </section>

  <section class="card card--contact" aria-label="Card back">
    <div class="contact-brand"><span class="brand-name">Kestra Loop</span></div>
    <div class="info-panel">
      <div class="info-block">
        <p class="person-name">DALE MORVEN</p>
        <p class="person-role">CO-FOUNDER | MANAGING DIRECTOR</p>
        <svg class="icon" viewBox="0 0 12 12" aria-hidden="true"><path d="M6 0a4 4 0 0 1 4 4c0 3-4 8-4 8S2 7 2 4a4 4 0 0 1 4-4zm0 2.3a1.7 1.7 0 1 0 0 3.4 1.7 1.7 0 0 0 0-3.4z"/></svg>
        <p class="contact-line">Plivorantu | ABN 38 614 207 923</p>
        <p class="contact-line">Suite 718 240 Wattlebrook Lane</p>
        <p class="contact-line">Melbourne Vic 3000</p>
        <div class="gap"></div>
        <svg class="icon" viewBox="0 0 12 12" aria-hidden="true"><path d="M2.4 0.5 4.3 2.6 3.3 4.1c.7 1.6 2 2.9 3.6 3.6l1.5-1 2.1 1.9-1.2 2.1C4.8 10.4 1.6 7.2.4 2.7z"/></svg>
        <p class="contact-line">+61 0487 259 318</p>
        <svg class="icon" viewBox="0 0 12 12" aria-hidden="true"><path d="M0 2h12v8H0zM1 3v.4l5 3.3 5-3.3V3z"/></svg>
        <p class="contact-line">dale.morven@plivorantu.com</p>
      </div>
      <div class="accent-strip"></div>
    </div>
  </section>
</main>
</body>
</html>
```